At Home Pet Euthanasia - business cards & brand stationary

We already have a logo and the colors and a website. Need a business card designed that will be able to customized to multiple veterinarians who will be partnering with us. The feel needs to be compassionate, comforting with our tagline 'A Gift of Love at Home'. It will be 2 sides.
On the back our platform/partner vets will be customizing each business card with their own service areas, phone numbers, name and title. On the front, i would like to see experimentation with use of our photos, the logo, tagline and a description 'Peaceful and Compassionate At-Home Pet Euthanasia'

```html
<!DOCTYPE html>
<html lang="en">
<head>
<meta charset="utf-8">
<title>Willowpaw Business Card</title>
<link href="https://fonts.googleapis.com/css2?family=Poppins:ital,wght@0,400;0,500;0,600;0,700;1,400;1,500&display=swap" rel="stylesheet">
<style>
  :root {
    --page: #ebe8e3;
    --card: #ffffff;
    --brand-blue: #7b9cc6;
    --navy: #1f2b4a;
    --heading-blue: #2f4c7c;
    --text-blue: #34507e;
    --rule: #9fb5d6;
    --plum-dark: #6f5b7c;
    --plum-light: #a481b2;
    --skin: #e7c3ae;
    --shirt: #e39b8c;
    --fur: #ecebec;
    --backdrop: #d9dde6;
  }
  * { box-sizing: border-box; margin: 0; padding: 0; }
  html, body { width: 900px; height: 1200px; overflow: hidden; }
  body {
    background: var(--page);
    font-family: "Poppins", Arial, sans-serif;
    position: relative;
  }
  .card {
    position: absolute;
    left: 82px;
    width: 733px;
    height: 428px;
    border-radius: 22px;
    overflow: hidden;
  }
  /* Contact side */
  .card-contact { top: 138px; background: var(--card); }
  .brand {
    position: absolute; left: 46px; top: 58px;
    display: flex; align-items: center; gap: 14px;
  }
  .brand-square { width: 40px; height: 40px; background: var(--brand-blue); border-radius: 4px; }
  .brand-name { font-size: 42px; font-weight: 600; color: var(--brand-blue); line-height: 1; }
  .person { position: absolute; right: 45px; top: 80px; text-align: right; }
  .person-name { font-size: 23px; font-weight: 700; color: var(--navy); letter-spacing: 0.5px; line-height: 1.1; }
  .person-title { font-size: 15px; font-weight: 500; color: var(--brand-blue); letter-spacing: 0.5px; margin-top: 2px; }
  .divider { position: absolute; left: 46px; top: 292px; width: 462px; height: 2px; background: var(--rule); }
  .areas-heading {
    position: absolute; right: 45px; top: 280px;
    font-size: 19px; font-weight: 600; color: var(--heading-blue); letter-spacing: 0.4px;
  }
  .contact-list { position: absolute; left: 46px; top: 312px; list-style: none; }
  .contact-list li {
    display: flex; align-items: center; gap: 10px;
    font-size: 16px; color: var(--text-blue); height: 23px;
  }
  .contact-list svg { width: 16px; height: 16px; fill: none; stroke: var(--text-blue); stroke-width: 1.6; }
  .area-list { position: absolute; top: 310px; list-style: none; text-align: right; }
  .area-list.col-one { right: 257px; }
  .area-list.col-two { right: 45px; }
  .area-list li {
    display: flex; justify-content: flex-end; align-items: center; gap: 8px;
    font-size: 16px; color: var(--text-blue); height: 23px;
  }
  .area-list .dot { width: 11px; height: 11px; border-radius: 50%; background: var(--brand-blue); }
  .edge-band { position: absolute; left: 0; bottom: 0; width: 100%; height: 15px; display: flex; }
  .edge-band .band-dark { width: 50%; background: var(--plum-dark); }
  .edge-band .band-light { width: 50%; background: var(--plum-light); }

  /* Brand side */
  .card-brand { top: 634px; background: var(--brand-blue); }
  .hero-photo {
    position: absolute; left: 0; top: 0; width: 520px; height: 100%;
    background:
      linear-gradient(90deg, rgba(123,156,198,0) 58%, var(--brand-blue) 100%),
      radial-gradient(ellipse 90px 140px at 60px 360px, var(--shirt) 0%, rgba(227,155,140,0) 100%),
      radial-gradient(ellipse 110px 120px at 120px 110px, var(--skin) 0%, rgba(231,195,174,0) 100%),
      radial-gradient(ellipse 130px 220px at 270px 230px, var(--fur) 0%, rgba(236,235,236,0) 100%),
      linear-gradient(90deg, #e3cfc3 0%, var(--backdrop) 45%, #c9d4e4 80%);
  }
  .brand-block { position: absolute; left: 440px; width: 280px; top: 112px; text-align: center; color: #fff; }
  .brand-circle { width: 100px; height: 100px; border-radius: 50%; background: #fff; margin: 0 auto 22px; }
  .brand-block .brand-name { color: #fff; font-size: 40px; }
  .tagline { font-size: 14px; font-style: italic; margin-top: 8px; }
  .description { font-size: 14.5px; font-weight: 500; font-style: italic; line-height: 20px; margin-top: 46px; letter-spacing: 0.2px; }
</style>
</head>
<body>

<section class="card card-contact">
  <div class="brand">
    <span class="brand-square"></span>
    <span class="brand-name">Willowpaw</span>
  </div>
  <div class="person">
    <div class="person-name">DANIEL REYES</div>
    <div class="person-title">VETERINARIAN</div>
  </div>

  <div class="divider"></div>
  <h2 class="areas-heading">SERVICE AREAS</h2>

  <ul class="contact-list">
    <li><svg viewBox="0 0 16 16"><path d="M4 2l2.5 3-1.5 1.5a8 8 0 0 0 4.5 4.5L11 9.5l3 2.5-1.5 2C7 14 2 9 2 3.5z"/></svg>555-014-2620</li>
    <li><svg viewBox="0 0 16 16"><rect x="2" y="4" width="12" height="9"/><path d="M2 4l6 5 6-5"/></svg>daniel@willowpaw.com</li>
    <li><svg viewBox="0 0 16 16"><circle cx="8" cy="8" r="6"/><path d="M2 8h12M8 2c-3 3-3 9 0 12M8 2c3 3 3 9 0 12"/></svg>www.willowpaw.com</li>
  </ul>

  <ul class="area-list col-one">
    <li>Mar Vista<span class="dot"></span></li>
    <li>Melrose Hill<span class="dot"></span></li>
    <li>Mid-City Heights<span class="dot"></span></li>
  </ul>
  <ul class="area-list col-two">
    <li>Manchester Square<span class="dot"></span></li>
    <li>Mandeville Canyon<span class="dot"></span></li>
    <li>Marina Peninsula<span class="dot"></span></li>
  </ul>

  <div class="edge-band"><span class="band-dark"></span><span class="band-light"></span></div>
</section>

<section class="card card-brand">
  <div class="hero-photo" role="img" aria-label="Photo of a young girl lovingly holding a blue-eyed tabby cat"></div>
  <div class="brand-block">
    <div class="brand-circle"></div>
    <div class="brand-name">Willowpaw</div>
    <p class="tagline">A gift of love at home.</p>
    <p class="description">Peaceful and Compassionate<br>At-Home Pet Euthanasia</p>
  </div>
</section>

</body>
</html>
```